Copper lark buildworks

Copper lark buildworks is a small construction company.
Who is a licenced builder, Carpenter, joiner,
working on heritage ,new build, speacial projects and sometimes furniture

Industry/Entity Type

Construction

```html
<!DOCTYPE html>
<html lang="en">
<head>
<meta charset="utf-8">
<title>Copper lark buildworks – business card</title>
<link rel="stylesheet" href="https://fonts.googleapis.com/css2?family=Lato:wght@400;700&family=Exo+2:wght@400&display=swap">
<style>
  :root {
    --page: #e9e6e2;
    --frost-top: #f3f2f0;
    --frost-bottom: #d9d6d2;
    --green: #5f9a2c;
    --green-bright: #7dbb3c;
    --black: #141414;
    --charcoal: #2a2a2a;
    --white: #f4f4f4;
    --silver: #c9c4bd;
    --ink: #1d1d1d;
  }
  * { box-sizing: border-box; margin: 0; padding: 0; }
  html, body { width: 970px; height: 1200px; overflow: hidden; }
  body {
    background: var(--page);
    font-family: "Lato", sans-serif;
    position: relative;
  }
  .card {
    position: absolute;
    left: 205px;
    top: 110px;
    width: 560px;
    height: 979px;
    border-radius: 22px;
    overflow: hidden;
    box-shadow: 0 10px 40px rgba(0,0,0,0.18);
  }
  .card-art { position: absolute; inset: 0; width: 100%; height: 100%; }
  .centered {
    position: absolute;
    left: 0;
    width: 100%;
    text-align: center;
    white-space: nowrap;
  }
  .brand-mark {
    position: absolute;
    left: 230px;
    top: 140px;
    width: 100px;
    height: 100px;
    border-radius: 50%;
    background: var(--green);
  }
  .brand-name {
    top: 296px;
    font-size: 40px;
    font-weight: 700;
    color: var(--ink);
    line-height: 1;
  }
  .holder-name {
    top: 540px;
    font-family: "Exo 2", sans-serif;
    font-size: 34px;
    line-height: 1;
    color: var(--white);
    letter-spacing: 0.5px;
  }
  .holder-name .surname { color: var(--green-bright); }
  .holder-role {
    top: 577px;
    font-size: 23px;
    line-height: 1;
    color: var(--white);
  }
  .phone-number, .email-address {
    font-size: 29px;
    line-height: 1;
    color: var(--white);
  }
  .phone-number { top: 711px; letter-spacing: 0.5px; }
  .email-address { top: 818px; }
  .web-address {
    top: 934px;
    font-size: 27px;
    font-weight: 700;
    line-height: 1;
    color: var(--ink);
    letter-spacing: 2px;
  }
</style>
</head>
<body>
  <div class="card">
    <svg class="card-art" viewBox="0 0 595 1040" preserveAspectRatio="none" aria-hidden="true">
      <defs>
        <linearGradient id="frost" x1="0" y1="0" x2="0" y2="1">
          <stop offset="0" stop-color="var(--frost-top)"/>
          <stop offset="1" stop-color="var(--frost-bottom)"/>
        </linearGradient>
        <linearGradient id="dark" x1="0" y1="0" x2="0" y2="1">
          <stop offset="0" stop-color="var(--black)"/>
          <stop offset="0.6" stop-color="var(--charcoal)"/>
          <stop offset="1" stop-color="var(--black)"/>
        </linearGradient>
        <linearGradient id="rule" x1="0" y1="0" x2="1" y2="0">
          <stop offset="0" stop-color="var(--green)" stop-opacity="0"/>
          <stop offset="0.5" stop-color="var(--green-bright)"/>
          <stop offset="1" stop-color="var(--green)" stop-opacity="0"/>
        </linearGradient>
      </defs>
      <rect class="frost-panel" width="595" height="1040" fill="url(#frost)"/>
      <path class="green-swoosh" d="M0,545 Q260,430 595,500 L595,520 Q300,468 0,580 Z" fill="var(--green)"/>
      <path class="dark-panel" d="M0,580 Q300,468 595,520 L595,975 L0,975 Z" fill="url(#dark)"/>
      <path class="black-swoosh" d="M115,540 Q350,470 595,505 L595,512 Q360,482 115,540 Z" fill="var(--black)"/>
      <rect class="silver-strip" x="0" y="968" width="595" height="10" fill="var(--silver)"/>
      <rect class="web-band" x="0" y="978" width="595" height="62" fill="var(--green)"/>
      <g class="phone-icon" fill="none" stroke="var(--green-bright)" stroke-width="3">
        <circle cx="297.5" cy="722" r="22"/>
        <rect x="290" y="709" width="15" height="26" rx="2"/>
        <line x1="295" y1="730" x2="300" y2="730"/>
      </g>
      <line class="contact-rule" x1="95" y1="803" x2="505" y2="803" stroke="url(#rule)" stroke-width="1.5"/>
      <g class="mail-icon" fill="none" stroke="var(--green-bright)" stroke-width="3">
        <circle cx="297.5" cy="840" r="22"/>
        <rect x="285" y="831" width="25" height="18" fill="var(--green-bright)" stroke="none"/>
        <polyline points="285,831 297.5,842 310,831" stroke="var(--black)" stroke-width="2"/>
        <line x1="285" y1="849" x2="294" y2="840" stroke="var(--black)" stroke-width="2"/>
        <line x1="310" y1="849" x2="301" y2="840" stroke="var(--black)" stroke-width="2"/>
      </g>
    </svg>

    <div class="brand-mark" aria-hidden="true"></div>
    <p class="centered brand-name">Copper lark buildworks</p>

    <p class="centered holder-name">Tomas <span class="surname">Reyland</span></p>
    <p class="centered holder-role">President</p>

    <p class="centered phone-number">0412557036</p>
    <p class="centered email-address">hello@copperlarkmail.com</p>

    <p class="centered web-address">www.copperlarkbuild.com</p>
  </div>
</body>
</html>
```